Luxury Business Card Design for High-End Window Treatments

Gilded Slatworks
Custom Plantation Shutters & Architectural Shading Systems

⸻

BACK

Daniel Trevick
Owner

Custom Interior & Exterior Window Treatments

919-555-0148
gildedslatworks.com

I have included a picture that I’m hoping we can use on the back, but I’m also wondering if you can get rid of the ladder? Should we get rid of shutters , shades and blinds underneath Gilded Slatworks?

Target Market(s)

High-end residential homeowners, custom home builders, architects, interior designers, and luxury renovation clients seeking premium plantation shutters and motorized architectural shading systems.

Industry/Entity Type

Custom Window treatments

Contact Information for Business Card

Front Gilded Slatworks Custom Plantation Shutters Motorized Architectural Shading Systems BACK Daniel Trevick Owner 919-555-0148 GildedSlatworks.com Custom Interior & Exterior Window Treatments By Appointment

Requirements
Nice to have
• Not 100% sure on nice to halves or the color but you can definitely check out my website to get a better understanding of what I’m trying to do

```html
<!DOCTYPE html>
<html lang="en">
<head>
<meta charset="utf-8">
<title>Gilded Slatworks – Business Card</title>
<link rel="stylesheet" href="https://fonts.googleapis.com/css2?family=Tinos:wght@400;700&display=swap">
<style>
  :root {
    --bg: #1c1c1e;
    --card: #050505;
    --cream: #f1ebdc;
    --gold: #f2c94c;
    --band: #f7d160;
    --band-text: #1d1a12;
    --white: #ffffff;
    --sky-top: #2d5f9c;
    --sky-mid: #8fb3d6;
    --house: #4a4d52;
  }
  * { margin: 0; padding: 0; box-sizing: border-box; }
  html, body {
    width: 1200px; height: 801px; overflow: hidden;
    background: var(--bg);
    font-family: "Tinos", "Times New Roman", serif;
  }
  .stage {
    width: 1200px; height: 801px;
    display: flex; align-items: center; justify-content: center; gap: 40px;
  }
  .card {
    position: relative;
    width: 540px; height: 309px;
    background: var(--card);
    border-radius: 22px;
    overflow: hidden;
    box-shadow: 0 10px 30px rgba(0,0,0,.5);
  }

  /* Front */
  .front .brand { position: absolute; left: 120px; top: 62px; }
  .brand-name {
    color: var(--cream);
    font-weight: 400;
    font-size: 44px;
    line-height: 1;
    letter-spacing: .5px;
  }
  .brand-name .line2 { display: block; padding-left: 38px; }
  .tagline {
    margin-top: 10px;
    padding-left: 38px;
    color: var(--gold);
    font-weight: 700;
    font-size: 19px;
    word-spacing: 14px;
  }
  .services {
    position: absolute; left: 70px; top: 210px;
    list-style: none;
    color: var(--white);
    font-size: 21px;
    line-height: 1.45;
  }
  .services li::before { content: "•"; margin-right: 8px; font-size: 14px; vertical-align: middle; }

  /* Back */
  .back .photo {
    position: absolute; left: 0; top: 0; width: 330px; height: 100%;
    background:
      linear-gradient(90deg, rgba(5,5,5,0) 55%, var(--card) 100%),
      linear-gradient(180deg, var(--sky-top) 0%, var(--sky-mid) 38%, var(--house) 60%, #3e4a33 100%);
  }
  .back .brand { position: absolute; left: 300px; top: 26px; }
  .back .brand-name { font-size: 34px; }
  .back .brand-name .line2 { padding-left: 28px; }
  .back .tagline { font-size: 14px; padding-left: 20px; word-spacing: 8px; margin-top: 7px; }
  .person { position: absolute; left: 320px; top: 138px; }
  .person-name { color: var(--gold); font-weight: 700; font-size: 25px; }
  .person-role { color: var(--white); font-size: 16px; margin: 2px 0 0 14px; }
  .contacts { list-style: none; margin: 8px 0 0 30px; color: var(--white); font-size: 17px; }
  .contacts li { display: flex; align-items: center; gap: 10px; line-height: 1.55; }
  .contacts svg { width: 17px; height: 17px; flex: none; }
  .band {
    position: absolute; left: 0; right: 0; top: 252px; height: 34px;
    background: var(--band);
    color: var(--band-text);
    font-weight: 700; font-size: 18px;
    display: flex; align-items: center; justify-content: center;
    letter-spacing: .2px;
  }
</style>
</head>
<body>
<main class="stage">
  <section class="card front" aria-label="Card front">
    <div class="brand">
      <div class="brand-name">Gilded<span class="line2">Slatworks</span></div>
      <div class="tagline">Shutters Shades Blinds</div>
    </div>
    <ul class="services">
      <li>Custom Plantation Shutters</li>
      <li>Motorized Architectural Shading Systems</li>
    </ul>
  </section>

  <section class="card back" aria-label="Card back">
    <div class="photo" role="img" aria-label="Photo of a large home with a covered porch fitted with exterior motorized shades"></div>
    <div class="brand">
      <div class="brand-name">Gilded<span class="line2">Slatworks</span></div>
      <div class="tagline">Shutters Shades Blinds</div>
    </div>
    <div class="person">
      <div class="person-name">Daniel Trevick</div>
      <div class="person-role">Owner</div>
      <ul class="contacts">
        <li>
          <svg viewBox="0 0 24 24" aria-hidden="true"><path fill="var(--gold)" d="M6.6 10.8a15 15 0 0 0 6.6 6.6l2.2-2.2a1 1 0 0 1 1-.25 11.4 11.4 0 0 0 3.6.57 1 1 0 0 1 1 1V20a1 1 0 0 1-1 1A17 17 0 0 1 3 4a1 1 0 0 1 1-1h3.5a1 1 0 0 1 1 1c0 1.25.2 2.45.57 3.57a1 1 0 0 1-.25 1z"/></svg>
          919-555-0148
        </li>
        <li>
          <svg viewBox="0 0 24 24" aria-hidden="true"><circle cx="12" cy="12" r="9" fill="none" stroke="var(--gold)" stroke-width="2.2"/><ellipse cx="12" cy="12" rx="4" ry="9" fill="none" stroke="var(--gold)" stroke-width="1.8"/><path d="M3 12h18" stroke="var(--gold)" stroke-width="1.8"/></svg>
          gildedslatworks.com
        </li>
      </ul>
    </div>
    <div class="band">Custom Interior &amp; Exterior Window Treatments By Appointment</div>
  </section>
</main>
</body>
</html>
```